Keto Food Brand Needs Packaging Design and Logo

We need a logo and packaging design for a stand-up food bag for our keto shake mix. We are a health and wellness brand launching our first shake mix product. I would like bold, bright colors. This document goes more in depth . This brand might encompass more than only food so I want the logo to be versatile for supplements and other health products. https://files.plavexa.net/doc/k7Rt2mQx9LpW4vZs8NcB3yHf6JdTa1Ue/view?share=link See images of logos attached. It doesn't have to be food for the logo but I like the creativity of the ones listed.

Target Market(s)

Keto. Health and Fitness

Logo Text

Zumora

Font styles to use
Serif
Sans Serif

Colors

Designer to choose colors to be used in the design.

```html
<!DOCTYPE html>
<html lang="en">
<head>
<meta charset="utf-8">
<title>Zumora Keto Cheesecake Shake Mix – Pouch Front</title>
<link href="https://fonts.googleapis.com/css2?family=Montserrat:wght@900&family=Oswald:wght@500;600;700&family=Poppins:wght@600&display=swap" rel="stylesheet">
<style>
  :root {
    --page-bg: #ececec;
    --foil: #f1f2f3;
    --foil-shade: #dfe1e3;
    --teal: #3cc7d8;
    --ink: #262b30;
    --ink-soft: #2e3a44;
    --badge-red: #e3262b;
    --white: #ffffff;
    --cream: #f3ecd0;
    --crust: #c58a52;
  }
  * { box-sizing: border-box; margin: 0; padding: 0; }
  html, body {
    width: 1126px;
    height: 1200px;
    overflow: hidden;
    background: var(--page-bg);
  }
  .canvas { position: relative; width: 1126px; height: 1200px; }
  .pouch {
    position: absolute;
    left: 163px; top: 55px;
    width: 800px; height: 1090px;
    border-radius: 14px;
    overflow: hidden;
    background: var(--teal);
  }
  .pouch__foil {
    position: absolute;
    left: 0; top: 0;
    width: 800px; height: 320px;
    background: linear-gradient(180deg, var(--foil-shade) 0%, var(--foil) 18%, var(--white) 55%, var(--foil) 100%);
  }
  .pouch__seal {
    position: absolute;
    left: 0; top: 92px;
    width: 800px; height: 2px;
    background: var(--foil-shade);
  }
  .brand {
    position: absolute;
    left: 0; top: 250px;
    width: 800px;
    text-align: center;
    font-family: "Poppins", sans-serif;
    font-weight: 600;
    font-size: 52px;
    letter-spacing: -1px;
    line-height: 1;
    color: var(--ink);
  }
  .keto {
    position: absolute;
    left: 262px; top: 330px;
    font-family: "Montserrat", sans-serif;
    font-weight: 900;
    font-size: 196px;
    line-height: 170px;
    letter-spacing: -4px;
    color: var(--ink);
  }
  .keto span { display: block; }
  .claims {
    position: absolute;
    left: 84px; top: 535px;
    width: 132px;
    font-family: "Oswald", sans-serif;
    font-weight: 500;
    font-size: 17px;
    line-height: 1.05;
    color: var(--ink);
    text-transform: uppercase;
    text-align: center;
  }
  .claims__item { padding: 5px 0; }
  .claims__item + .claims__item { border-top: 2px solid var(--ink); }
  .badge {
    position: absolute;
    left: 619px; top: 548px;
    width: 104px; height: 104px;
    border-radius: 50%;
    background: var(--badge-red);
    border: 3px solid var(--white);
    color: var(--white);
    font-family: "Oswald", sans-serif;
    font-weight: 600;
    text-align: center;
    transform: rotate(-12deg);
    padding-top: 14px;
  }
  .badge__number { display: block; font-size: 38px; line-height: 1; }
  .badge__label { display: block; font-size: 15px; letter-spacing: 0.5px; line-height: 1.2; }
  .product-shot {
    position: absolute;
    left: 628px; top: 742px;
    width: 150px; height: 212px;
    border-radius: 10px;
    background: linear-gradient(180deg, var(--white) 0%, var(--cream) 70%, var(--crust) 100%);
  }
  .flavor {
    position: absolute;
    left: 270px; top: 770px;
    width: 340px;
    font-family: "Oswald", sans-serif;
    font-weight: 700;
    color: var(--ink-soft);
    text-transform: uppercase;
    line-height: 1;
    text-align: center;
  }
  .flavor__name { display: block; font-size: 62px; letter-spacing: 0.5px; }
  .flavor__type { display: block; font-size: 42px; margin-top: 6px; }
  .net-weight {
    position: absolute;
    left: 62px; top: 962px;
    font-family: "Oswald", sans-serif;
    font-weight: 500;
    font-size: 22px;
    color: var(--ink);
  }
  .supplement-label {
    position: absolute;
    left: 517px; top: 972px;
    font-family: "Oswald", sans-serif;
    font-weight: 600;
    font-size: 21px;
    letter-spacing: 1px;
    color: var(--ink);
    text-transform: uppercase;
    word-spacing: 6px;
  }
</style>
</head>
<body>
<div class="canvas">
  <div class="pouch">
    <div class="pouch__foil"></div>
    <div class="pouch__seal"></div>

    <div class="brand">Zumora</div>

    <div class="keto"><span>KE</span><span>TO</span></div>

    <div class="claims">
      <div class="claims__item">No artificial flavors</div>
      <div class="claims__item">All natural</div>
      <div class="claims__item">Keto-friendly &amp; low carb</div>
    </div>

    <div class="badge">
      <span class="badge__number">20</span>
      <span class="badge__label">SERVINGS</span>
    </div>

    <div class="product-shot" role="img" aria-label="Photo of a cheesecake slice with a milk splash"></div>

    <div class="flavor">
      <span class="flavor__name">Cheesecake</span>
      <span class="flavor__type">Shake Mix</span>
    </div>

    <div class="net-weight">Net Wt: 1.02 LB.</div>
    <div class="supplement-label">Dietary Supplement</div>
  </div>
</div>
</body>
</html>
```